New Business Card Design Project

I'd like a business card design around the same modern style that I used on my website www.brovanhs.com
It's gonna be one of those round corners double-sided business cards with maybe a big logo on the front and all the info on the back of the card.

Contact Information for Business Card

Marco Delgado
425-317-6084
www.brovanhs.com

www.facebook.com/BrovanHomeServices
www.intsgram.com/BrovanHomeServices

Requirements
Must have
• it needs to look elegant and modern

```html
<!DOCTYPE html>
<html lang="en">
<head>
<meta charset="utf-8">
<title>Brovan Home Services – Business Card</title>
<link rel="stylesheet" href="https://fonts.googleapis.com/css2?family=Work+Sans:wght@400;500;700&display=swap">
<style>
  :root {
    --bg: #ecebe8;
    --card-black: #15171a;
    --card-charcoal: #2b2d30;
    --card-white: #ffffff;
    --brand-blue: #1d8fd8;
    --text-light: #e9eaec;
    --edge-blue: #1a76b8;
  }
  * { box-sizing: border-box; margin: 0; padding: 0; }
  html, body { width: 1200px; height: 715px; overflow: hidden; }
  body {
    background: var(--bg);
    font-family: "Work Sans", Arial, sans-serif;
    position: relative;
  }
  .card {
    position: absolute;
    top: 209px;
    width: 520px;
    height: 297px;
    border-radius: 18px;
    overflow: hidden;
    box-shadow: 0 10px 28px rgba(0,0,0,0.18);
  }
  .card-front {
    left: 50px;
    background: var(--card-black);
    border-bottom: 4px solid var(--edge-blue);
    display: flex;
    align-items: center;
    justify-content: center;
  }
  .card-back { left: 630px; background: var(--card-white); }
  .card-back .shapes { position: absolute; inset: 0; }
  .brand-name {
    display: flex;
    align-items: center;
    gap: 12px;
    color: var(--brand-blue);
    font-weight: 700;
    font-size: 34px;
    letter-spacing: 0.5px;
    line-height: 1;
  }
  .brand-dot {
    width: 18px; height: 18px;
    border-radius: 50%;
    background: var(--brand-blue);
    flex: none;
  }
  .card-back .brand-name {
    position: absolute;
    left: 282px;
    right: 20px;
    top: 124px;
    font-size: 23px;
    line-height: 1.05;
    gap: 9px;
  }
  .card-back .brand-dot { width: 14px; height: 14px; }
  .contact {
    position: absolute;
    left: 24px;
    top: 56px;
    color: var(--text-light);
    font-size: 13px;
    line-height: 1.45;
  }
  .contact-name {
    color: var(--brand-blue);
    font-size: 18px;
    font-weight: 500;
    letter-spacing: 1px;
    text-transform: uppercase;
    line-height: 1.15;
  }
  .contact-title { font-size: 13px; margin-bottom: 12px; }
  .contact-address { margin-bottom: 6px; }
  .contact-list { list-style: none; }
  .contact-list li { display: flex; align-items: center; gap: 8px; }
  .contact-list svg { width: 10px; height: 10px; flex: none; }
</style>
</head>
<body>

  <section class="card card-front" aria-label="Card front">
    <div class="brand-name"><span class="brand-dot"></span>Brovan Home Services</div>
  </section>

  <section class="card card-back" aria-label="Card back">
    <svg class="shapes" viewBox="0 0 520 297" preserveAspectRatio="none">
      <path d="M0 0 H270 C205 90 210 210 320 297 H0 Z" fill="var(--card-charcoal)"/>
      <path d="M270 0 C205 90 210 210 320 297" fill="none" stroke="var(--brand-blue)" stroke-width="4"/>
    </svg>

    <div class="contact">
      <div class="contact-name">Marco Delgado</div>
      <div class="contact-title">Director</div>
      <div class="contact-address">2417 Alder Creek Road<br>Tulsa, OK 74105</div>
      <ul class="contact-list">
        <li>
          <svg viewBox="0 0 10 10"><path d="M2 1 L4 1 L4.6 3 L3.5 3.8 C4 5 5 6 6.2 6.5 L7 5.4 L9 6 L9 8 C5 8.5 1.5 5 2 1 Z" fill="var(--text-light)"/></svg>
          425-317-6084
        </li>
        <li>
          <svg viewBox="0 0 10 10"><rect x="1" y="2" width="8" height="6" fill="none" stroke="var(--text-light)" stroke-width="1"/><path d="M1 2 L5 5.5 L9 2" fill="none" stroke="var(--text-light)" stroke-width="1"/></svg>
          info@brovanhs.com
        </li>
        <li>
          <svg viewBox="0 0 10 10"><circle cx="5" cy="5" r="4" fill="none" stroke="var(--text-light)" stroke-width="1"/><path d="M1 5 H9 M5 1 C3 3 3 7 5 9 M5 1 C7 3 7 7 5 9" fill="none" stroke="var(--text-light)" stroke-width="0.8"/></svg>
          www.brovanhs.com
        </li>
        <li>
          <svg viewBox="0 0 10 10"><circle cx="5" cy="5" r="4" fill="var(--text-light)"/></svg>
          /BrovanHomeServices
        </li>
        <li>
          <svg viewBox="0 0 10 10"><rect x="1" y="1" width="8" height="8" fill="var(--text-light)"/></svg>
          /BrovanHomeServices
        </li>
      </ul>
    </div>

    <div class="brand-name"><span class="brand-dot"></span>Brovan Home Services</div>
  </section>

</body>
</html>
```